4th Generation Family Business Needs a New Card Design!

We are a family owned 4th Generation company. We are based in the Sydney, Australia area and we are desperately in need of a more modern and classy card. We are monumental masons who design, supply & erect lasting memorials throughout cemeteries in Sydney. Our customers are normally in a period of grieving. I have attached logo files that will need to be implemented on the card. Company was established 1935. Australian Owned and Operated. Card needs to be designed to PIXO.com specification.

Target Market(s)

Our target market is based upon people that a grieving for family members that have passed away. We also deal with alot of companies that own and operate cemeteries.

Industry/Entity Type

Business

Contact Information for Business Card

Simon Harcourt, Operations Manager, 0417293086, simon@harcourtmemorials.com.au
Lewis Harcourt, Director, 0491630572, lewis@harcourtmemorials.com.au
Phone # 02 9561 3048
Website: www.harcourtmemorials.com.au
Address: Suite 17, 8 Palfrey Lane, West Carlow, Sydney NSW 2156

Font styles to use
Serif
Decorative
Script

Requirements
Must have
• Would like to see the logo nicely implemented with a modern design. Embossed lettering would be a nice additive.

```html
<!DOCTYPE html>
<html lang="en">
<head>
<meta charset="utf-8">
<title>Harcourt Memorials – Business Card</title>
<link href="https://fonts.googleapis.com/css2?family=Cinzel:wght@400;500&family=Tinos&display=swap" rel="stylesheet">
<style>
  :root {
    --backdrop: #e4e4e4;
    --card: #fbfbfb;
    --card-shade: #efefef;
    --ink: #1c1c1c;
    --ink-soft: #3a3a3a;
    --gold: #d4a91f;
    --gold-deep: #c2961a;
  }
  html, body {
    margin: 0;
    padding: 0;
    overflow: hidden;
  }
  body {
    width: 1200px;
    height: 576px;
    background: var(--backdrop);
    position: relative;
    font-family: "Tinos", "Times New Roman", serif;
  }
  .card {
    position: absolute;
    top: 138px;
    width: 485px;
    height: 294px;
    background: linear-gradient(180deg, var(--card) 0%, var(--card-shade) 100%);
    box-shadow: 0 2px 5px rgba(0,0,0,0.22);
    overflow: hidden;
  }
  .card--front { left: 82px; }
  .card--back { left: 602px; width: 482px; height: 291px; }
  .card__band {
    position: absolute;
    left: 0; right: 0; bottom: 0;
    height: 10px;
    background: linear-gradient(180deg, var(--gold) 0%, var(--gold-deep) 100%);
  }
  .brand-name {
    position: absolute;
    font-family: "Cinzel", "Times New Roman", serif;
    font-weight: 500;
    color: var(--ink);
    text-align: center;
    line-height: 1.1;
    letter-spacing: 0.5px;
  }
  .card--front .brand-name {
    left: 0; right: 0;
    top: 112px;
    font-size: 34px;
  }
  .card--back .brand-name {
    left: 20px;
    width: 196px;
    top: 108px;
    font-size: 26px;
  }
  .contact-block {
    position: absolute;
    left: 236px;
    top: 62px;
    color: var(--ink-soft);
  }
  .contact-block__name {
    margin: 0;
    font-family: "Cinzel", "Times New Roman", serif;
    font-weight: 500;
    font-size: 19px;
    color: var(--ink);
    letter-spacing: 0.5px;
  }
  .contact-block__title {
    margin: 2px 0 14px;
    font-size: 12px;
  }
  .contact-list {
    list-style: none;
    margin: 0;
    padding: 0;
    font-size: 12.5px;
  }
  .contact-list li {
    display: flex;
    align-items: center;
    height: 17.5px;
  }
  .contact-list svg {
    width: 9px;
    height: 9px;
    margin: 0 13px 0 4px;
    fill: var(--gold);
  }
  .contact-block__address {
    margin: 8px 0 0;
    font-size: 12.5px;
    line-height: 18px;
  }
</style>
</head>
<body>

  <section class="card card--front">
    <div class="brand-name">Harcourt<br>Memorials</div>
    <div class="card__band"></div>
  </section>

  <section class="card card--back">
    <div class="brand-name">Harcourt<br>Memorials</div>

    <div class="contact-block">
      <h1 class="contact-block__name">Simon Harcourt</h1>
      <p class="contact-block__title">Operations Manager</p>
      <ul class="contact-list">
        <li>
          <svg viewBox="0 0 10 10" aria-hidden="true"><path d="M2 0.5 L3.6 2.6 L2.8 3.6 Q4 6 6.4 7.2 L7.4 6.4 L9.5 8 L8.4 9.5 Q3.5 9 0.5 1.6 Z"/></svg>
          0491630572
        </li>
        <li>
          <svg viewBox="0 0 10 10" aria-hidden="true"><path d="M0 3 Q5 0 10 3 L10 4.5 L7.5 4.5 L7.5 3.5 L2.5 3.5 L2.5 4.5 L0 4.5 Z M2 5 L8 5 L9 9.5 L1 9.5 Z"/></svg>
          02 9561 3048
        </li>
        <li>
          <svg viewBox="0 0 10 10" aria-hidden="true"><path d="M0 2 L10 2 L5 5.8 Z M0 3 L5 6.8 L10 3 L10 8.5 L0 8.5 Z"/></svg>
          lewis@harcourtmemorials.com.au
        </li>
        <li>
          <svg viewBox="0 0 10 10" aria-hidden="true"><circle cx="5" cy="5" r="4.5"/></svg>
          www.harcourtmemorials.com.au
        </li>
      </ul>
      <p class="contact-block__address">Suite 17, 8 Palfrey Lane,<br>West Carlow, Sydney NSW 2156</p>
    </div>

    <div class="card__band"></div>
  </section>

</body>
</html>
```